Enlighted Feel-Good Wrapper Design for Cannabis Snack Bar: Vesko Bites.

We need a logo and wrapper for the first product in our line-up, Pip Crackle Maple! - Honey Salted Nuts and Dark Chocolate. Please highlight the name Maple Pip Crackle!, more than the name Vesko Bites or flavor of the bar. The package dimensions unfolded and unsealed are 6.5 inches x 5.25 inches. I have uploaded 3 photos of similar bar wrappers as an example of the wrapper type. The winning design will be awarded an extra amount for the Vesko Bites logo from Craft Hive.

It is a nut based snack bar similar to brands like Brisk, Stellar Munch, Orla, and Rover Bars. The difference is that this bar will contain THC and/or CBD oils. It is designed for the Medical Marijuana market in California. I would like the bar to be more upscale in design as we are going after a demographic with a higher disposable income and will be in their 30's-60's. We would like the brand to be appealing to both men and women. We would like the wrapper/logo to have an air of enlightenment to it. We want people to feel like they will be at peace when they eat this bar. Please do not make the design flashy, or decorated with marijuana leaves. We do not want something cheesy. We uploaded pictures of the bar so you can see what they look like. The packaging has to be OPAQUE.

Please include all the following. If you don't know specific values, weights or ingredients please fill the space with any text that can be substituted.

Label Regulatory Requirements:

(1) The identity of the product in a text size reasonably related to the most prominent printed matter on the panel;
(2) The words “cannabis-infused” immediately above the identity of the product in bold type and a text size larger than the text size used for the identity of the product;
(3) The cannabis product symbol uploaded in this post. The symbol shall be no smaller in size than half (.5) inch by half (.5) inch and shall be printed legibly and conspicuously;
(4) The net weight or volume of the contents of the package;

1.4 oz (40g)

(5) The THC content and CBD content for the package in its entirety, expressed in milligrams per package;

40mg

(6) The THC content and CBD content per serving, expressed in milligrams per serving;

10mg

(b) The primary panel text must be in type size no less than 6 point font and be in relation to the size of the primary panel and container.

40408. Informational Panel Labeling Requirements.
(a) The label for a medical cannabis product shall include an informational panel that includes the following:
(1) The licensed manufacturer and its contact number or website address;

Vesko Bites, San Diego, CA (555)302-7194, www.veskobites.example

(2) The date of manufacture;
(3) Each of the following statements:
(A) “SCHEDULE I CONTROLLED SUBSTANCE.”
(B) “KEEP OUT OF REACH OF CHILDREN AND ANIMALS” in bold print.
(C) “FOR MEDICAL USE ONLY.”
(D) “IF PREGNANT OR BREASTFEEDING, CONSULT A PHYSICIAN PRIOR TO USE.”
(E) “THE INTOXICATING EFFECTS OF THIS PRODUCT MAY BE DELAYED BY UP TO TWO HOURS.”
(F) “THIS PRODUCT MAY IMPAIR THE ABILITY TO DRIVE OR OPERATE MACHINERY, PLEASE USE EXTREME CAUTION.”
(4) A list of all product ingredients in descending order of predominance by weight or volume;

NUT MIXTURE:
almonds, peanuts, walnuts, puffed rice, flaxseed

SYRUP:
honey, brown rice syrup, sea salt, vanilla

CHOCOLATE DRIZZLE:
dark chocolate, coconut oil

(5) If an edible product that contains an ingredient, flavoring, coloring, or an incidental additive that bears or contains a major food allergen, the word “contains,” followed by a list of the applicable major food allergens;

Contains tree nuts.

(6) If an edible product, the names of any artificial food colorings contained in the product;
(7) If an edible product, the amount, in grams, of sodium, sugar, carbohydrates, and total fat per serving;

Dark Chocolate Sea Salt: 193 calories, 12.5g fat, 95mg sodium, 18.9g carbs, 2.1g fiber, 14g sugars, 5.2g protein

(8) The lot number;
(9) Instructions for use, such as the method of consumption or application, and any preparation necessary prior to use;
(10) The product expiration date, “use by” date, or “best by” date; and
(11) The unique identifier.
(b) The informational panel text shall be in a type size of no less than 6 point font and in relation to the size of the primary panel and container, unless there is insufficient area on the container available to print all the required information in a type size of no less than 6 point font. In such a case, the label shall include the warning statements required by paragraph (3) in a type size of no less than 6 point font, and the product shall be accompanied by a supplemental labeling that includes all of the information required by this section. The text of the supplemental labeling shall be no less than 8 point font.

The label shall not contain any of the following:

(a) Claims that the manufactured cannabis or cannabis product was grown in a California county when the cannabis was not grown there.
(b) The name of a California county unless the cannabis was grown there.
(c) Content that is or designed to be attractive to individuals under the age of 21, including but not limited to:
(1) Cartoons;
(2) Any likeness to images, characters, or phrases that are popularly used to advertise to children; or
(3) Any imitation of candy packaging or labeling.
(d) False labeling information. Labeling is false if it is false or misleading in any particular.
(e) Claims of health benefits or other physical benefits.
Updates

Industry/Entity Type

Retail

Logo Text

Vesko Bites

Colors

Designer to choose colors to be used in the design.

Requirements
Must have
• I would like to have a logo/icon of an cute owl or icon of a small tree branch with leaves and nut hanging off or anything else that you think would be a good logo incorporated with the company name "Vesko Bites." I uploaded a logo of an owl logo that I like. Feel free to adjust and create something creative, please do not copy it.
• The wrapper needs to reflect an upscale, natural, farm fresh, whole food product. We are trying to build a high end line of products that appeal to health conscious women and men ages 30 - 60 years old.
• Please include text from Allergen warning in one of the uploaded photos.
• Please add - "Gluten free" to the label, "Non GMO" or "GMO Free" and "No Soy" or "Soy Free", and "Dairy Free" as either writing or as an icon of some sort.
Nice to have
• Please see posted photos of some wrappers of food products that I like for ideas. Some color suggestions to incorporate: Red, Yellow, Green, Orange simply because these colors have been proven appealing to the eye for food labels. You may use one or a few of these and can balance them out with other colors. Please do not use traditional colors associated with cannabis such as dark brown or deep green. Subdued, natural looking versions of these may be okay if they are balanced out with other colors or the rest of the bar. I would also like the wrapper to have some graphics that can illustrate what the bar actually looks like so that people know whats inside!
• The final design should communicate:
• Freshness
• Organic
• Healthy
• Modern
Should not have
• I do not want this product to have graphics of typical cheesy cannabis/marijuana leaves or any other low class graphics related to the industry. Not graphics of marijuana flower, joints, smoke or leaves.

```html
<!DOCTYPE html>
<html lang="en">
<head>
<meta charset="utf-8">
<title>Vesko Bites – Maple, Pip Crackle! Bar Wrappers</title>
<link rel="stylesheet" href="https://fonts.googleapis.com/css2?family=Josefin+Sans:wght@600&family=Oswald:wght@600&family=Open+Sans:wght@400&family=Libre+Baskerville:wght@700&display=swap">
<style>
  :root {
    --backdrop: #959595;
    --kraft: #c9ae8a;
    --kraft-end: #bda07a;
    --foil: #eef0f2;
    --foil-end: #dfe2e6;
    --seal-red: #c8202a;
    --seal-red-dark: #a8181f;
    --honey: #f4bd28;
    --cocoa: #3a1d12;
    --bar-light: #d9c08e;
    --bar-dark: #5a2e1c;
    --warning-blue: #3fa9d8;
    --slate: #6b7480;
    --paper: #ffffff;
  }
  html, body {
    margin: 0;
    width: 1200px;
    height: 1200px;
    overflow: hidden;
    background: var(--backdrop);
  }
  .canvas {
    position: relative;
    width: 1200px;
    height: 1200px;
  }
  .wrapper {
    position: absolute;
    left: 92px;
    width: 1012px;
    height: 372px;
    display: block;
  }
  .wrapper--kraft { top: 104px; }
  .wrapper--foil { top: 568px; }

  .wrapper--kraft .wrapper-body { fill: var(--kraft); }
  .wrapper--kraft .wrapper-end { fill: var(--kraft-end); }
  .wrapper--foil .wrapper-body { fill: var(--foil); }
  .wrapper--foil .wrapper-end { fill: var(--foil-end); }

  .seal-band { fill: var(--seal-red); }
  .seal-crimp { stroke: var(--seal-red-dark); stroke-width: 2; }
  .end-crimp { stroke: rgba(0,0,0,0.08); stroke-width: 2; }

  .honey-swash { fill: var(--honey); }
  .infused-flag { fill: var(--seal-red); }
  .infused-text {
    font-family: "Libre Baskerville", Georgia, serif;
    font-weight: 700;
    font-size: 13px;
    fill: var(--paper);
  }
  .net-weight {
    font-family: "Open Sans", Arial, sans-serif;
    font-size: 28px;
    fill: var(--cocoa);
  }
  .brand-name {
    font-family: "Josefin Sans", Arial, sans-serif;
    font-weight: 600;
    font-size: 34px;
    fill: var(--cocoa);
    letter-spacing: 2px;
  }
  .brand-dot { fill: var(--honey); }
  .product-name {
    font-family: "Josefin Sans", Arial, sans-serif;
    font-weight: 600;
    font-size: 50px;
    fill: var(--paper);
    stroke: var(--cocoa);
    stroke-width: 2.5px;
    paint-order: stroke;
  }
  .product-suffix {
    font-family: "Josefin Sans", Arial, sans-serif;
    font-weight: 600;
    font-size: 24px;
    fill: var(--cocoa);
  }
  .flavor {
    font-family: "Oswald", Arial, sans-serif;
    font-weight: 600;
    font-size: 28px;
    letter-spacing: 2px;
    fill: var(--cocoa);
  }
  .claims {
    font-family: "Open Sans", Arial, sans-serif;
    font-size: 13.5px;
  }
  .wrapper--kraft .claims { fill: var(--paper); }
  .wrapper--foil .claims { fill: var(--slate); }
  .potency {
    font-family: "Open Sans", Arial, sans-serif;
    font-size: 12px;
    fill: var(--cocoa);
  }
  .warning-symbol {
    fill: var(--seal-red);
    stroke: var(--warning-blue);
    stroke-width: 3;
  }
</style>
</head>
<body>
<main class="canvas">

  <svg class="wrapper wrapper--kraft" viewBox="0 0 1012 372" aria-label="Kraft paper wrapper">
    <defs>
      <linearGradient id="bar-tones-kraft" x1="0" x2="1" y1="0" y2="0">
        <stop offset="0" stop-color="#5a2e1c"/>
        <stop offset="0.35" stop-color="#d9c08e"/>
        <stop offset="0.65" stop-color="#8a4a2a"/>
        <stop offset="1" stop-color="#d9c08e"/>
      </linearGradient>
    </defs>
    <rect class="wrapper-body" x="0" y="0" width="1012" height="372"/>
    <rect class="wrapper-end" x="956" y="0" width="56" height="372"/>
    <g class="end-crimp">
      <line x1="966" y1="6" x2="966" y2="366"/>
      <line x1="978" y1="6" x2="978" y2="366"/>
      <line x1="990" y1="6" x2="990" y2="366"/>
      <line x1="1002" y1="6" x2="1002" y2="366"/>
    </g>
    <rect class="seal-band" x="0" y="0" width="68" height="372"/>
    <g class="seal-crimp">
      <line x1="10" y1="6" x2="10" y2="366"/>
      <line x1="22" y1="6" x2="22" y2="366"/>
      <line x1="34" y1="6" x2="34" y2="366"/>
      <line x1="46" y1="6" x2="46" y2="366"/>
      <line x1="58" y1="6" x2="58" y2="366"/>
    </g>

    <rect x="172" y="52" width="784" height="90" rx="30" fill="url(#bar-tones-kraft)" role="img" aria-label="Photo of the nut bar with dark chocolate drizzle"/>

    <path class="honey-swash" d="M290 150 L930 138 L944 170 L930 200 L900 232 L905 262 L870 270 L300 276 L280 240 L300 205 L282 175 Z"/>

    <path class="infused-flag" d="M92 78 L210 78 L140 176 Z"/>
    <text class="infused-text" x="151" y="95" text-anchor="middle">CANNABIS</text>
    <text class="infused-text" x="151" y="108" text-anchor="middle">INFUSED</text>

    <text class="net-weight" x="90" y="198">40g</text>

    <circle class="brand-dot" cx="226" cy="170" r="10"/>
    <text class="brand-name" x="226" y="230" text-anchor="middle">VESKO</text>
    <text class="brand-name" x="226" y="268" text-anchor="middle">BITES</text>

    <text class="product-name" x="326" y="208">MAPLE, PIP CRACKLE!</text>
    <text class="product-suffix" x="880" y="206">BAR</text>
    <text class="flavor" x="362" y="242">SALTED DARK CHOCOLATE &amp; NUTS</text>

    <text class="claims" x="376" y="305">• NON-GMO • GLUTEN-FREE • NO SOY • DAIRY-FREE</text>
    <text class="potency" x="758" y="294">THC content 40mg/pack</text>
    <text class="potency" x="758" y="308">CBD content 10mg/serving</text>

    <path class="warning-symbol" d="M844 56 L932 56 L886 128 Z"/>
  </svg>

  <svg class="wrapper wrapper--foil" viewBox="0 0 1012 372" aria-label="White foil wrapper">
    <defs>
      <linearGradient id="bar-tones-foil" x1="0" x2="1" y1="0" y2="0">
        <stop offset="0" stop-color="#5a2e1c"/>
        <stop offset="0.35" stop-color="#d9c08e"/>
        <stop offset="0.65" stop-color="#8a4a2a"/>
        <stop offset="1" stop-color="#d9c08e"/>
      </linearGradient>
    </defs>
    <rect class="wrapper-body" x="0" y="0" width="1012" height="372"/>
    <rect class="wrapper-end" x="956" y="0" width="56" height="372"/>
    <g class="end-crimp">
      <line x1="966" y1="6" x2="966" y2="366"/>
      <line x1="978" y1="6" x2="978" y2="366"/>
      <line x1="990" y1="6" x2="990" y2="366"/>
      <line x1="1002" y1="6" x2="1002" y2="366"/>
    </g>
    <rect class="seal-band" x="0" y="0" width="68" height="372"/>
    <g class="seal-crimp">
      <line x1="10" y1="6" x2="10" y2="366"/>
      <line x1="22" y1="6" x2="22" y2="366"/>
      <line x1="34" y1="6" x2="34" y2="366"/>
      <line x1="46" y1="6" x2="46" y2="366"/>
      <line x1="58" y1="6" x2="58" y2="366"/>
    </g>

    <rect x="172" y="52" width="784" height="90" rx="30" fill="url(#bar-tones-foil)" role="img" aria-label="Photo of the nut bar with dark chocolate drizzle"/>

    <path class="honey-swash" d="M290 150 L930 138 L944 170 L930 200 L900 232 L905 262 L870 270 L300 276 L280 240 L300 205 L282 175 Z"/>

    <path class="infused-flag" d="M92 78 L210 78 L140 176 Z"/>
    <text class="infused-text" x="151" y="95" text-anchor="middle">CANNABIS</text>
    <text class="infused-text" x="151" y="108" text-anchor="middle">INFUSED</text>

    <text class="net-weight" x="90" y="198">40g</text>

    <circle class="brand-dot" cx="226" cy="170" r="10"/>
    <text class="brand-name" x="226" y="230" text-anchor="middle">VESKO</text>
    <text class="brand-name" x="226" y="268" text-anchor="middle">BITES</text>

    <text class="product-name" x="326" y="208">MAPLE, PIP CRACKLE!</text>
    <text class="product-suffix" x="880" y="206">BAR</text>
    <text class="flavor" x="362" y="242">SALTED DARK CHOCOLATE &amp; NUTS</text>

    <text class="claims" x="376" y="305">• NON-GMO • GLUTEN-FREE • NO SOY • DAIRY-FREE</text>
    <text class="potency" x="758" y="294">THC content 40mg/pack</text>
    <text class="potency" x="758" y="308">CBD content 10mg/serving</text>

    <path class="warning-symbol" d="M844 56 L932 56 L886 128 Z"/>
  </svg>

</main>
</body>
</html>
```